BOLD & MINIMALIST DESIGN NEEDED

We want a very bold but minimalistic business card design that is impactful and utilizes both sides of the business card. Our current logo is included for your use.

We want bold fonts and good use of negative space. We don't want the logo to overpower the design.

Target Market(s)

Professionals who are building new commercial buildings.

Industry/Entity Type

Construction

Contact Information for Business Card

Name, Title, email, office phone, cell phone, website

Font styles to use
Serif
Sans Serif

Requirements
Must have
• Bold design!

```html
<!DOCTYPE html>
<html lang="en">
<head>
<meta charset="utf-8">
<title>Ridgeline Design + Build — Business Card</title>
<link rel="stylesheet" href="https://fonts.googleapis.com/css2?family=Source+Sans+3:wght@600;700&display=swap">
<style>
  :root {
    --backdrop: #e5e5e5;
    --card-dark: #0a0c0b;
    --card-light: #ffffff;
    --ink: #0b0b0b;
    --paper-text: #f7f7f5;
    --accent: #93f20f;
    --mark-gray: #6a6a6a;
    --card-edge: #9a9a9a;
    --shadow: rgba(0, 0, 0, 0.7);
  }
  * { box-sizing: border-box; margin: 0; padding: 0; }
  html, body {
    width: 1200px;
    height: 1200px;
    overflow: hidden;
    background: var(--backdrop);
    font-family: "Source Sans 3", "Source Sans Pro", Arial, sans-serif;
  }
  .canvas { position: relative; width: 1200px; height: 1200px; }
  .card {
    position: absolute;
    left: 272px;
    width: 642px;
    height: 357px;
    box-shadow: 8px 7px 6px var(--shadow);
  }
  .card--front { top: 203px; background: var(--card-dark); }
  .card--back {
    top: 625px;
    background: var(--card-light);
    border: 1px solid var(--card-edge);
    color: var(--ink);
  }
  .brand-front {
    position: absolute;
    left: 0; right: 0; top: 150px;
    display: flex;
    align-items: center;
    justify-content: center;
    gap: 16px;
    color: var(--paper-text);
    font-weight: 700;
  }
  .brand-front__square { width: 34px; height: 34px; background: var(--accent); }
  .brand-front__name {
    font-size: 44px;
    letter-spacing: 2px;
    line-height: 1;
    text-transform: uppercase;
  }
  .brand-back {
    position: absolute;
    right: 14px; top: 60px;
    display: flex;
    align-items: center;
    gap: 6px;
    color: var(--mark-gray);
    font-weight: 700;
    font-size: 17px;
    letter-spacing: 0.5px;
    text-transform: uppercase;
  }
  .brand-back__square { width: 12px; height: 12px; background: var(--mark-gray); }
  .contact-name {
    position: absolute;
    left: 29px; top: 46px;
    font-size: 47px;
    font-weight: 700;
    line-height: 1;
  }
  .contact-title {
    position: absolute;
    left: 29px; top: 111px;
    font-size: 25px;
    font-weight: 600;
    line-height: 1;
  }
  .contact-list {
    position: absolute;
    left: 29px; top: 200px;
    list-style: none;
    font-size: 19px;
    font-weight: 600;
    line-height: 1;
  }
  .contact-list li { height: 30px; }
  .contact-list li.gap { margin-top: 8px; }
</style>
</head>
<body>
  <main class="canvas">
    <section class="card card--front" aria-label="Card front">
      <div class="brand-front">
        <span class="brand-front__square"></span>
        <span class="brand-front__name">Ridgeline Design + Build</span>
      </div>
    </section>

    <section class="card card--back" aria-label="Card back">
      <div class="brand-back">
        <span class="brand-back__square"></span>
        <span>Ridgeline Design + Build</span>
      </div>
      <h1 class="contact-name">NAME LASTNAME</h1>
      <p class="contact-title">YOUR TITTLE</p>
      <ul class="contact-list">
        <li>EMAIL@WEBSITE.COM</li>
        <li class="gap">123 - 456 - 7890</li>
        <li>123 - 456 - 7890</li>
        <li class="gap">YOURWEBSITE.COM</li>
      </ul>
    </section>
  </main>
</body>
</html>
```